Velmor Spire Nine Flash website

we need a website to cater to 2 aspect of the business. We have Velmor spire residence and velmor spire office. For the office, we will get their inquire and arrange a face to face meetup to show them the office area for rent. For the residence side, it will need to be like staylane or roomvio.com. we want to allow them to book online for the date they need. We have a total of 10 different room configurations starting at $70 per night and up depending on the size of the room. example of the design is https://brisquelodge.com/

Target Market(s)

the website should have detail information on the layout, designs, and luxury of the building.

Industry/Entity Type

office and service appartment rental/lease

Coding

Coded - Design and coding required

Number of Pages Required

5+ page

Requirements
Must have
• a luxury perspective
Nice to have
• example https://brisquelodge.com/

```html
<!DOCTYPE html>
<html lang="en">
<head>
<meta charset="utf-8">
<title>Velmor Spire Nine</title>
<link href="https://fonts.googleapis.com/css2?family=Montserrat:ital,wght@0,400;0,500;0,600;0,700;1,400;1,500;1,600;1,700&display=swap" rel="stylesheet">
<style>
:root{
  --gold:#c99a2e;
  --gold-soft:#d9b25a;
  --ink:#1e1e1e;
  --muted:#555;
  --white:#fff;
  --paper:#ffffff;
  --footer:#f7f5f0;
  --bar:#141414;
}
*{box-sizing:border-box;margin:0;padding:0}
html,body{width:1200px;height:5140px;overflow:hidden}
body{position:relative;background:var(--paper);font-family:"Montserrat",sans-serif;color:var(--ink)}
.abs{position:absolute}
.photo{position:absolute}
.btn{display:inline-block;background:var(--gold);color:var(--white);font-size:14px;font-weight:500;padding:12px 26px;border-radius:3px}

/* hero */
.hero{left:0;top:0;width:1200px;height:650px;background:linear-gradient(160deg,#2f4a66 0%,#243a52 45%,#1a2838 100%)}
.hero-tower{left:380px;top:40px;width:260px;height:610px;background:linear-gradient(180deg,#7c6b55,#4a3d31 60%,#2a231d)}
.nav{left:40px;top:28px;width:1120px;height:44px;display:flex;align-items:center;justify-content:space-between}
.logo{display:flex;align-items:center;gap:8px;color:var(--gold-soft);font-size:13px;font-weight:600}
.logo i{width:12px;height:12px;background:var(--gold-soft);display:block}
.nav-links{display:flex;align-items:center;gap:34px;font-size:14px;color:var(--white)}
.nav-links .on{color:var(--gold-soft)}
.hero-title{left:40px;top:245px;color:var(--white);font-style:italic;font-weight:700;font-size:80px;line-height:1.2}
.hero-copy{left:800px;top:255px;width:360px;color:var(--white);font-style:italic;font-size:15px;line-height:1.45}
.hero-btn{left:800px;top:480px}

/* sections */
.h2{font-style:italic;font-weight:600;font-size:36px;color:var(--ink)}
.rule{height:1px;background:var(--gold)}
.body{font-style:italic;font-size:15px;line-height:1.5;color:var(--muted)}

.welcome-bar{left:40px;top:720px;width:4px;height:46px;background:var(--gold)}
.welcome-title{left:62px;top:722px}
.welcome-copy{left:40px;top:790px;width:1120px}

.divider{left:600px;top:3420px;width:1px;height:110px;background:var(--gold)}
.rooms-title{left:0;top:3555px;width:1200px;text-align:center;font-weight:600;font-style:italic;font-size:42px}
.rooms-copy{left:210px;top:3625px;width:780px;text-align:center;font-size:15px;line-height:1.5;color:var(--ink)}
.card-name{font-style:italic;font-weight:600;font-size:20px;text-align:center;width:350px}
.card-copy{font-size:14px;line-height:1.4;text-align:center;width:350px;color:var(--ink)}
.rooms-foot{left:40px;top:4265px;width:880px;font-size:15px;line-height:1.5}
.rooms-btn{left:1025px;top:4275px}

/* cta */
.cta{left:0;top:4420px;width:1200px;height:350px;background:linear-gradient(180deg,#3a3a3a 0%,#5a4b3e 55%,#8a7458 100%)}
.cta-title{left:0;top:4495px;width:1200px;text-align:center;color:var(--white);font-style:italic;font-weight:600;font-size:38px;line-height:1.25}
.cta-copy{left:330px;top:4610px;width:540px;text-align:center;color:var(--white);font-size:14px;line-height:1.5}
.cta-btn{left:540px;top:4700px}

/* footer */
.footer{left:0;top:4770px;width:1200px;height:330px;background:var(--footer)}
.f-logo{left:40px;top:4810px}
.f-tag{left:40px;top:4845px;width:200px;font-size:12px;line-height:1.4;color:var(--muted)}
.f-head{font-size:17px;font-weight:600;color:var(--ink)}
.f-list{list-style:none;font-size:14px;line-height:2;color:var(--ink)}
.f-contact{font-size:14px;line-height:1.5;color:var(--ink);display:flex;gap:10px;align-items:flex-start;width:300px}
.f-contact svg{flex:0 0 16px;margin-top:2px}
.sub-input{left:750px;top:4880px;width:240px;height:42px;border:1px solid #cfc9bd;background:#e9e6df;font-size:13px;color:#888;padding:12px 14px}
.sub-btn{left:1010px;top:4880px;height:42px;width:130px;text-align:center}
.bottom{left:0;top:5100px;width:1200px;height:40px;background:var(--bar);color:var(--white);font-size:12px;display:flex;align-items:center;justify-content:space-between;padding:0 40px}
</style>
</head>
<body>

<!-- hero -->
<section class="abs hero" role="img" aria-label="Dusk sky behind a tall residential tower"></section>
<div class="photo hero-tower" role="img" aria-label="High-rise tower facade rising into the sky"></div>
<nav class="abs nav">
  <div class="logo"><i></i>Velmor Spire Nine</div>
  <div class="nav-links">
    <span class="on">Home</span><span>About Us</span><span>Room</span><span>Experience</span>
    <span class="btn">Contact Us</span>
  </div>
</nav>
<h1 class="abs hero-title">Privileges<br>and<br>Comfort</h1>
<p class="abs hero-copy">A place where warmth and luxury come together. Explore a blissful living or working experience in this special location. With the best facilities and stunning views, Velmor Spire invites you to experience the coolness of an elegant and inspiring lifestyle. Come discover beauty in every corner, and experience the perfect balance of modern comfort and traditional charm, only at Velmor Spire.</p>
<span class="abs btn hero-btn">Contact Us</span>

<!-- welcome -->
<div class="abs welcome-bar"></div>
<h2 class="abs h2 welcome-title">Welcome to Velmor Spire!</h2>
<p class="abs body welcome-copy">We are more than just a building, we are the home of your dreams. At Velmor Spire, we are committed to providing an unforgettable living and working experience, where comfort meets luxury.</p>
<div class="photo" style="left:40px;top:960px;width:1120px;height:365px;background:linear-gradient(180deg,#eeeeec,#cfcac4 60%,#8a7a6a)" role="img" aria-label="Modern white kitchen with steel appliances and bar stools"></div>

<!-- feature rows -->
<h2 class="abs h2" style="left:40px;top:1640px">Irreplaceable Experience</h2>
<div class="abs rule" style="left:40px;top:1700px;width:540px"></div>
<p class="abs body" style="left:40px;top:1730px;width:480px">We are committed to providing an unforgettable stay that exceeds your expectations and leaves lasting memories.</p>
<div class="photo" style="left:610px;top:1520px;width:550px;height:390px;background:linear-gradient(135deg,#9a9aa0,#c8c6c4 50%,#6e6a68)" role="img" aria-label="Guest relaxing on a sofa by a bright window"></div>

<div class="photo" style="left:40px;top:2000px;width:550px;height:390px;background:linear-gradient(135deg,#b8b2aa,#e2ddd6 55%,#8c857c)" role="img" aria-label="Freestanding bathtub in a stone-tiled bathroom"></div>
<h2 class="abs h2" style="left:680px;top:2140px">Best quality</h2>
<div class="abs rule" style="left:680px;top:2200px;width:480px"></div>
<p class="abs body" style="left:680px;top:2230px;width:440px">We only provide the best facilities that meet standards of excellence.</p>

<h2 class="abs h2" style="left:40px;top:2610px">Ultimate Luxury</h2>
<div class="abs rule" style="left:40px;top:2670px;width:540px"></div>
<p class="abs body" style="left:40px;top:2700px;width:480px">From the magnificent interior design to the exclusive facilities, we guarantee that every detail at Velmor Spire reflects the highest standards of luxury.</p>
<div class="photo" style="left:610px;top:2470px;width:550px;height:390px;background:linear-gradient(180deg,#4a3a2c,#8a6a48 50%,#3f8aa8)" role="img" aria-label="Indoor swimming pool with warm wooden walls"></div>

<div class="photo" style="left:40px;top:2950px;width:550px;height:390px;background:linear-gradient(135deg,#e8e4de,#c9c2b8 55%,#a05048)" role="img" aria-label="Bright living room with a red armchair and tall windows"></div>
<h2 class="abs h2" style="left:680px;top:3085px">Innovation</h2>
<div class="abs rule" style="left:680px;top:3145px;width:480px"></div>
<p class="abs body" style="left:680px;top:3175px;width:470px">We continually innovate to improve the resident experience and provide creative solutions for your business needs.</p>

<!-- rooms -->
<div class="abs divider"></div>
<h2 class="abs rooms-title">Find Your Dream Room</h2>
<p class="abs rooms-copy">Enjoy an unforgettable stay at Velmor Spire with the variety of room choices we offer. From cozy rooms for solo travelers to luxurious suites for large families, each of our rooms is designed with attention to detail and your comfort. <strong>Prices Start From $70 per Night</strong></p>

<div class="photo" style="left:40px;top:3740px;width:350px;height:380px;background:linear-gradient(180deg,#d8d6d2,#a9a39b 60%,#6a5e52)" role="img" aria-label="Standard room with a bed facing a city window"></div>
<div class="photo" style="left:425px;top:3740px;width:350px;height:380px;background:linear-gradient(180deg,#3a3532,#6e625a 60%,#2a2624)" role="img" aria-label="Exclusive suite with dark wood and a lounge area"></div>
<div class="photo" style="left:810px;top:3740px;width:350px;height:380px;background:linear-gradient(180deg,#c9bfb2,#a8967f 60%,#6a5a48)" role="img" aria-label="Family room with a large bed and soft lighting"></div>

<h3 class="abs card-name" style="left:40px;top:4140px">Standard Room</h3>
<p class="abs card-copy" style="left:40px;top:4172px">A comfortable, classy space with all the facilities you need for a pleasant stay.</p>
<h3 class="abs card-name" style="left:425px;top:4140px">Exclusive Suite</h3>
<p class="abs card-copy" style="left:425px;top:4172px">Bring a touch of luxury to your stay with our spacious and elegant suites.</p>
<h3 class="abs card-name" style="left:810px;top:4140px">Family Room</h3>
<p class="abs card-copy" style="left:810px;top:4172px">Share precious moments with your family in our spacious and comfortable rooms.</p>

<p class="abs rooms-foot">With affordable prices starting from <strong>$70</strong> per night, Velmor Spire provides a luxurious experience without breaking the bank. Find a room that suits your needs and budget, and make unforgettable memories at Velmor Spire.</p>
<span class="abs btn rooms-btn">See More</span>

<!-- call to action -->
<section class="abs cta" role="img" aria-label="Sunset seen through a window past a bathtub"></section>
<h2 class="abs cta-title">Find Your Dream Room in the<br>Blink of an Eye</h2>
<p class="abs cta-copy">If you have further questions or want to see our official plans or stay at Velmor Spire, contact our specialists at any time, ready to help you!</p>
<span class="abs btn cta-btn">Contact Us</span>

<!-- footer -->
<footer class="abs footer"></footer>
<div class="abs logo f-logo"><i></i>Velmor Spire Nine</div>
<p class="abs f-tag">Your home and office address for refined city living and work.</p>

<h4 class="abs f-head" style="left:280px;top:4810px">Site Resources</h4>
<ul class="abs f-list" style="left:280px;top:4845px">
  <li>Home</li><li>About Us</li><li>Room</li><li>Experience</li><li>Contact Us</li>
</ul>

<h4 class="abs f-head" style="left:475px;top:4810px">Connect With Halcyra Studio</h4>
<div class="abs f-contact" style="left:475px;top:4850px">
  <svg width="16" height="16" viewBox="0 0 24 24"><path fill="#1e1e1e" d="M6.6 10.8a15 15 0 0 0 6.6 6.6l2.2-2.2a1 1 0 0 1 1-.25 11.4 11.4 0 0 0 3.6.6 1 1 0 0 1 1 1V20a1 1 0 0 1-1 1A17 17 0 0 1 3 4a1 1 0 0 1 1-1h3.5a1 1 0 0 1 1 1c0 1.25.2 2.45.6 3.6a1 1 0 0 1-.25 1z"/></svg>
  <span>(555) 014-2290</span>
</div>
<div class="abs f-contact" style="left:475px;top:4885px">
  <svg width="16" height="16" viewBox="0 0 24 24"><rect x="2" y="5" width="20" height="14" rx="1" fill="none" stroke="#1e1e1e" stroke-width="2"/><path d="M2 6l10 7 10-7" fill="none" stroke="#1e1e1e" stroke-width="2"/></svg>
  <span>hello@halcyrastudio.test</span>
</div>
<div class="abs f-contact" style="left:475px;top:4920px">
  <svg width="16" height="16" viewBox="0 0 24 24"><path fill="#1e1e1e" d="M12 2a7 7 0 0 0-7 7c0 5 7 13 7 13s7-8 7-13a7 7 0 0 0-7-7zm0 9.5A2.5 2.5 0 1 1 12 6.5a2.5 2.5 0 0 1 0 5z"/></svg>
  <span>418 Harrow Lane, Suite 600,<br>Ashford Vale</span>
</div>

<h4 class="abs f-head" style="left:750px;top:4810px">Subscribe To Our Newsletter</h4>
<p class="abs" style="left:750px;top:4843px;font-size:13px;color:var(--muted)">Stay Updated With Exclusive Offers And Industry News</p>
<div class="abs sub-input">Your Email Address</div>
<span class="abs btn sub-btn">Submit</span>

<div class="abs bottom">
  <span>VELMOR SPIRE NINE © 2024. All rights reserved.</span>
  <span>Privacy Policy · Terms and Conditions</span>
</div>

</body>
</html>
```